zAvora Corporate Website

zAvora is a well-funded start up developing an Online Marketing Platform for small businesses in Europe.
We are launching in February 2012 with all-in-one online marketing services including professional website, DIY SEO, Dashboard with Reports and Online marketing tools, and Support.
Our internal web designer has come up with a preliminary website design which we wish to continue to improve using new ideas, colours, layout, image, etc.
The brief is very simple - improve the website whether it is look & feel, ease of use, conversion rate - we are looking for overall improvements.
The contest will last 5 days and we will award the winner £300.
If you are the winner , you will also be required to provide designs for 3 more internal pages adhering to the proposed home page design.
Judging criteria : -
Visual Design
Layout must adhere to best practices and wire frame. If you decide to move elements around significantly please provide reason
Functional, informative and drives calls to action
Industry/Entity Type
Marketing
Look and feel
Each slider illustrates characteristics of the customer's brand and the style your logo design should communicate.

```html
<!DOCTYPE html>
<html lang="en">
<head>
<meta charset="utf-8">
<title>zAvora – Online Marketing for Small Business</title>
<link rel="stylesheet" href="https://fonts.googleapis.com/css2?family=PT+Sans:wght@400;700&family=PT+Sans+Narrow:wght@700&family=Source+Sans+3:wght@400;600&display=swap">
<style>
:root{
  --blue:#2a9fd6;
  --blue-dark:#1a86bb;
  --blue-text:#1f95c9;
  --orange:#f07c2a;
  --ink:#333;
  --ink-soft:#555;
  --body:#3a3a3a;
  --line:#d4d4d4;
  --footer:#e4e4e4;
  --photo-top:#e3cfc1;
  --photo-mid:#ebe7e4;
  --photo-low:#dcdde0;
}
*{box-sizing:border-box;margin:0;padding:0}
html,body{width:874px;height:1200px;overflow:hidden}
body{position:relative;background:linear-gradient(#fff 0,#f1f1f1 587px,#ececec 588px,#f3f3f3 1063px);font-family:Arial,Helvetica,sans-serif;color:var(--body)}
.abs{position:absolute}
.top-links{left:764px;top:8px;font-size:11px;color:#222}
.top-links span{margin:0 6px;color:#666}
.brand{left:35px;top:45px;display:flex;align-items:center;gap:5px;font-family:"Source Sans 3",sans-serif;font-size:25px;color:#444}
.brand-dot{width:24px;height:24px;border-radius:50%;background:var(--blue)}
.main-nav{left:429px;top:47px;width:411px;height:30px;border:1px solid #ccc;border-radius:3px;background:linear-gradient(#fff,#ededed);display:flex;font-family:"Source Sans 3",sans-serif;font-size:14px}
.main-nav a{flex:1;text-align:center;line-height:28px;color:#222;text-decoration:none;border-left:1px solid #ddd}
.main-nav a:first-child{flex:0 0 83px;border:0;background:linear-gradient(#48b8e6,#2196cc);color:#fff}
.hero{left:34px;top:93px;width:806px;height:287px;border:1px solid #d8d8d8;border-radius:4px;background:linear-gradient(#fff,#f0f0f0);overflow:hidden}
.hero-photo{position:absolute;left:52px;top:34px;width:440px;height:253px;border-radius:6px 6px 0 0;background:linear-gradient(180deg,var(--photo-top) 0%,var(--photo-mid) 55%,var(--photo-low) 100%)}
.bubble{position:absolute;padding:3px 8px;border:1px solid #c5dbe8;border-radius:4px;background:#eef6fb;font-family:"Source Sans 3",sans-serif;font-size:15px;color:#2f6b86;white-space:nowrap}
.hero-title{position:absolute;left:518px;top:182px;font-family:"Source Sans 3",sans-serif;font-size:23px;line-height:24px;color:var(--orange)}
.btn{display:inline-block;border:1px solid var(--blue-dark);border-radius:3px;background:linear-gradient(#5cc6ee,#2596cd);color:#fff;font-family:"Source Sans 3",sans-serif;text-align:center;box-shadow:0 1px 2px rgba(0,0,0,.3)}
.hero .btn{position:absolute;left:677px;top:247px;width:96px;height:26px;line-height:24px;font-size:15px;color:#073a55}
.features{left:34px;top:390px;display:flex;gap:2px}
.feature{position:relative;width:200px;height:93px;border:1px solid #cfcfcf;background:linear-gradient(#fff,#e6e6e6);display:flex;align-items:center;gap:10px;padding-left:14px;font-family:"PT Sans Narrow",sans-serif;font-weight:700;color:#111}
.feature.active{border-top:3px solid var(--orange)}
.feature.active::before{content:"";position:absolute;left:92px;top:-11px;border:8px solid transparent;border-bottom-color:var(--orange)}
.feature-icon{width:42px;height:42px;border-radius:6px;flex:none}
.feature-text small{display:block;font-size:20px;line-height:21px;font-weight:700}
.feature-text strong{display:block;font-size:32px;line-height:32px;font-weight:700}
.tagline{left:0;width:874px;top:507px;text-align:center;font-family:"Source Sans 3",sans-serif;font-size:24px;color:var(--ink-soft)}
.quote{left:0;width:874px;top:541px;text-align:center;font-family:"Source Sans 3",sans-serif;font-weight:600;font-size:17px;color:var(--blue-text)}
.quote b{font-size:26px;vertical-align:-3px}
.divider{left:0;top:587px;width:874px;border-top:1px solid var(--line)}
h2{font-family:"Source Sans 3",sans-serif;font-weight:600;font-size:25px;color:var(--ink);line-height:28px}
h3{font-family:"Source Sans 3",sans-serif;font-weight:600;font-size:17px;color:#222;line-height:20px}
p{font-size:11px;line-height:15.3px;text-align:justify;hyphens:auto}
.more{display:block;text-align:right;font-family:"Source Sans 3",sans-serif;font-style:italic;font-size:15px;color:var(--blue-text)}
.col-left{left:34px;top:611px;width:395px}
.col-right{left:447px;top:611px;width:393px}
.thumbs{left:34px;top:713px;display:flex;gap:17px}
.thumb{width:120px;height:85px;border-radius:2px}
.tile{width:190px}
.tile-icon{position:absolute;width:44px;height:44px;border-radius:6px}
.tile-body{position:absolute;width:137px}
.newsletter{left:447px;top:946px}
.newsletter h2{font-weight:400;font-size:21px;color:#444}
.email{margin-top:8px;width:204px;height:30px;border:2px solid #ccc;border-radius:3px;background:#f6f6f6;padding-left:9px;font-size:13px;font-style:italic;color:#888;line-height:26px}
.newsletter .btn{position:absolute;left:127px;top:70px;width:77px;height:28px;line-height:26px;font-size:16px;color:#073a55}
.follow{left:706px;top:946px}
.follow h2{font-weight:400;font-size:21px;color:#222}
.social{display:flex;gap:7px;margin-top:6px}
.social span{width:28px;height:28px;border-radius:50%}
.footer{left:0;top:1063px;width:874px;height:137px;border-top:1px solid #c8c8c8;background:var(--footer)}
.footer-mark{position:absolute;left:35px;top:12px;width:65px;height:65px;border-radius:50%;background:#cfcfcf}
.footer ul{position:absolute;top:10px;list-style:none;font-size:10px;line-height:14px;color:#333}
.copyright{position:absolute;left:35px;top:94px;font-size:10px;color:#222}
</style>
</head>
<body>
<div class="abs top-links">Home<span>|</span>Login</div>
<div class="abs brand"><span class="brand-dot"></span>zAvora</div>
<nav class="abs main-nav"><a>About Us</a><a>Quick Tour</a><a>Pricing</a><a>Contact Us</a></nav>

<section class="abs hero">
  <div class="hero-photo" role="img" aria-label="Photo of a puzzled young man in a light shirt scratching his head"></div>
  <span class="bubble" style="left:21px;top:24px">SEO?</span>
  <span class="bubble" style="left:92px;top:18px">Reports?</span>
  <span class="bubble" style="left:181px;top:14px">Refferals?</span>
  <span class="bubble" style="left:50px;top:60px">Banners?</span>
  <span class="bubble" style="left:146px;top:56px">Content?</span>
  <span class="bubble" style="left:111px;top:98px">Support?</span>
  <span class="bubble" style="left:59px;top:112px">PPC?</span>
  <span class="bubble" style="left:305px;top:14px">Friendly?</span>
  <span class="bubble" style="left:411px;top:19px">Maintenence?</span>
  <span class="bubble" style="left:337px;top:56px">Testimonials?</span>
  <span class="bubble" style="left:459px;top:61px">Promotions?</span>
  <span class="bubble" style="left:537px;top:24px">Directories?</span>
  <span class="bubble" style="left:646px;top:10px">Website?</span>
  <span class="bubble" style="left:634px;top:47px">Images?</span>
  <span class="bubble" style="left:562px;top:66px">Chirper?</span>
  <span class="bubble" style="left:360px;top:98px">Email Marketing?</span>
  <span class="bubble" style="left:508px;top:102px">Searchly?</span>
  <span class="bubble" style="left:397px;top:127px">Blogs?</span>
  <div class="hero-title">Getting a Website<br>has never been so simple.</div>
  <a class="btn">SingUp Now</a>
</section>

<div class="abs features">
  <div class="feature active"><span class="feature-icon" style="background:#2f7fc8" role="img" aria-label="Globe icon"></span><div class="feature-text"><small>Business</small><strong>Website</strong></div></div>
  <div class="feature"><span class="feature-icon" style="background:linear-gradient(90deg,#e84c3d 33%,#f5b21b 33% 66%,#2d9ad6 66%)" role="img" aria-label="Bar chart icon"></span><div class="feature-text"><small>Online</small><strong>Marketing</strong></div></div>
  <div class="feature"><span class="feature-icon" style="background:#d83a2e;border-radius:50%" role="img" aria-label="Gauge icon"></span><div class="feature-text"><small>Dashboard</small><strong>Controls</strong></div></div>
  <div class="feature"><span class="feature-icon" style="background:#ef6a2b;border-radius:50%" role="img" aria-label="Lifebuoy icon"></span><div class="feature-text"><small>Full Setup</small><strong>&amp; Support</strong></div></div>
</div>

<div class="abs tagline">The Complete Online Marketing Solution for Small Business Website</div>
<div class="abs quote"><b>“</b> We set up everything in 3 hours You manage it-15 mins per week We provide full support <b>”</b></div>
<div class="abs divider"></div>

<section class="abs col-left">
  <h2>Featured Projects</h2>
  <p style="margin-top:5px">Lorem ipsum dolor sit amet, consec tetuer adipiscing elit. Praesent vestibulum molestie lacus. Aenean nonummy hendrerit mauris. Phasellus porta. Fusce suscipit varius mi.</p>
  <a class="more" style="margin-top:1px">View All</a>
</section>
<div class="abs thumbs">
  <div class="thumb" role="img" aria-label="Project screenshot: colourful dark portfolio site" style="background:linear-gradient(135deg,#2a2a2a 40%,#e8a23a 60%,#d9443b)"></div>
  <div class="thumb" role="img" aria-label="Project screenshot: green personal designer portfolio" style="background:linear-gradient(#1f3a20,#3f6b2c)"></div>
  <div class="thumb" role="img" aria-label="Project screenshot: bright green design studio site" style="background:linear-gradient(#4fae35,#2f8a22)"></div>
</div>

<div class="abs tile" style="left:34px;top:836px">
  <span class="tile-icon" style="left:2px;top:4px;background:#8a5a32" role="img" aria-label="Briefcase icon"></span>
  <div class="tile-body" style="left:52px"><h3>Case Study</h3><p>Lorem ipsum dolor sit amet, consec tetuer adipiscing elit. Praesent vestibulum molestie lacus.</p></div>
</div>
<div class="abs tile" style="left:239px;top:836px">
  <span class="tile-icon" style="left:4px;top:0;background:#f2c12e;border-radius:50%" role="img" aria-label="Light bulb icon"></span>
  <div class="tile-body" style="left:52px"><h3>How to Learn</h3><p>Lorem ipsum dolor sit amet, consec tetuer adipiscing elit. Praesent vestibulum molestie lacus.</p></div>
</div>
<div class="abs tile" style="left:34px;top:949px">
  <span class="tile-icon" style="left:0;top:0;background:linear-gradient(135deg,#6cb33f 50%,#e8e8e8 50%)" role="img" aria-label="Chat user icon"></span>
  <div class="tile-body" style="left:52px"><h3>News &amp; Chat</h3><p>Lorem ipsum dolor sit amet, consec tetuer adipiscing elit. Praesent vestibulum molestie lacus.</p></div>
</div>
<div class="abs tile" style="left:239px;top:949px">
  <span class="tile-icon" style="left:-4px;top:0;background:#5d8fc7" role="img" aria-label="Magnifying glass over screen icon"></span>
  <div class="tile-body" style="left:52px"><h3>Demo</h3><p>Lorem ipsum dolor sit amet, consec tetuer adipiscing elit. Praesent vestibulum molestie lacus.</p></div>
</div>

<section class="abs col-right">
  <h2>Why Choose Us?</h2>
  <p style="margin-top:5px">We started zAvora with a simple idea, to get online marketing to work for small businesses. We want to change the way small business owners acquire and keep customers.</p>
  <p style="margin-top:15px">Cloud technology makes it all possible. It allows us to deliver a robust, scalable and highly automated system for a small monthly fee. It also allows for seamless integration with powerful sales tools while ensuring ease of use.</p>
  <a class="more" style="margin-top:2px;margin-right:3px">Read More</a>
  <h2 style="margin-top:7px">How does it work ?</h2>
  <p style="margin-top:3px">Lorem ipsum dolor sit amet, consec tetuer adipiscing elit. Praesent vestibulum molestie lacus. Aenean nonummy hendrerit mauris. Phasellus porta. Fusce suscipit varius mi.</p>
  <p>Lorem ipsum dolor sit amet, consec tetuer adipiscing elit. Praesent vestibulum molestie lacus. Aenean nonummy hendrerit mauris. Phasellus porta. Fusce suscipit varius mi.</p>
  <a class="more" style="margin-top:-1px;margin-right:3px">Read More</a>
</section>

<section class="abs newsletter">
  <h2>SingUp for NewsLetter</h2>
  <div class="email">Enter Email Address</div>
  <a class="btn">Submit</a>
</section>
<section class="abs follow">
  <h2>Follow us</h2>
  <div class="social">
    <span style="background:#3b63b0" aria-label="Social network 1"></span>
    <span style="background:#3fa9e0" aria-label="Social network 2"></span>
    <span style="background:#1d74b2" aria-label="Social network 3"></span>
    <span style="background:#f07a26" aria-label="News feed"></span>
  </div>
</section>

<footer class="abs footer">
  <span class="footer-mark"></span>
  <ul style="left:171px"><li>Search Marketing</li><li>Organic / Natrual (SEO)</li><li>Social Media</li><li>Web Analytics</li></ul>
  <ul style="left:378px"><li>Contact Us</li><li>Customer Support</li><li>Request a call back</li><li>FAQ's</li></ul>
  <ul style="left:583px"><li>Site Map</li><li>Terms &amp; Conditions</li></ul>
  <div class="copyright">Copyright © 2012 by zAvora.com. All Rights Reserved</div>
</footer>
</body>
</html>
```